Brightgate Audio Video Security LLC

Need help designing a web page for an alarm company. I want to promote my business.

Target Market(s)

Residential and commercial clients

Industry/Entity Type

Security Service

Coding

Coded - Design and coding required

Number of Pages Required

2 page

Font styles to use
Sans Serif

Requirements
Must have
• I would llike my logo displayed on the page. I would like my slogan displayed as well
´´A GREAT PLACE FOR YOUR SECURITY NEEDS´´
We are licensed and insured
Company phone number 832-555-0147
Company hours: Monday-Friday 8am-5pm Company address: P.O. Box 419 Marren Falls, NV 77519 over 25 years experience
Email info. Brightgatesys@kelvamail.com
Company license #K41862509
Fire license# MTQ-6071852
LUV-8146027
We offer alarm monitoring,security cameras, access control,gate openers, home theater systems, covert camera installations, FIre alarm installation and monitoring
Nice to have
• We offer security at competitive prices.
Get customer information for a free quote similar to qmr website.
Should not have
• No prices listed on website

```html
<!DOCTYPE html>
<html lang="en">
<head>
<meta charset="utf-8">
<title>Brightgate Audio Video Security</title>
<link href="https://fonts.googleapis.com/css2?family=Poppins:wght@400;500;600;700;800&family=Lato:wght@400;700&display=swap" rel="stylesheet">
<style>
:root{
  --red:#d3202a;
  --red-dark:#a8141d;
  --ink:#141414;
  --text:#333;
  --muted:#8a8a8a;
  --grey-bg:#f1f1f1;
  --line:#e2e2e2;
  --footer:#121212;
  --white:#fff;
}
*{box-sizing:border-box;margin:0;padding:0}
html,body{width:1200px;height:4515px;overflow:hidden}
body{font-family:'Poppins',sans-serif;color:var(--text);background:var(--white);position:relative}
section,header,footer{position:absolute;left:0;width:1200px}
.red{color:var(--red)}
.nowrap{white-space:nowrap}
.btn{position:absolute;display:flex;align-items:center;justify-content:center;background:linear-gradient(90deg,var(--red),var(--red-dark));color:var(--white);font-weight:600;letter-spacing:.5px;border-radius:4px 4px 14px 4px;text-transform:uppercase;white-space:nowrap}
.section-title{position:absolute;left:0;width:1200px;text-align:center;font-weight:800;font-size:46px;color:var(--ink);letter-spacing:.5px}
.section-sub{position:absolute;left:260px;width:680px;text-align:center;font-size:18px;line-height:25px;color:#333}

/* hero */
.hero{top:0;height:643px;overflow:hidden}
.hero-photo{position:absolute;inset:0;background:linear-gradient(100deg,#f7f3ef 0%,#efe6dd 40%,#c9b4a2 62%,#4a3a33 78%,#2a2422 100%)}
.logo{position:absolute;left:110px;top:40px;display:flex;align-items:center;gap:10px}
.logo-dot{width:26px;height:26px;border-radius:50%;background:var(--red)}
.logo-name{font-weight:700;font-size:26px;color:var(--ink);letter-spacing:1px}
.nav{position:absolute;top:62px;left:347px;font-size:14px;color:#222}
.nav a{position:absolute;white-space:nowrap;text-decoration:none;color:#222}
.nav .active{color:var(--red)}
.nav .active::after{content:"";position:absolute;left:0;right:0;top:26px;height:2px;background:var(--red)}
.nav-divider{position:absolute;left:1027px;top:60px;width:1px;height:22px;background:#333}
.search{position:absolute;left:1070px;top:62px}
.hero-title{position:absolute;left:110px;top:222px;font-weight:700;font-size:42px;line-height:50px;color:var(--ink);white-space:nowrap}
.hero-text{position:absolute;left:110px;top:340px;width:450px;font-size:13.5px;line-height:21px;color:#222}

/* who */
.who{top:643px;height:492px}
.who h2{position:absolute;left:110px;top:70px;font-weight:800;font-size:46px;color:var(--ink);white-space:nowrap}
.who .lead{position:absolute;left:110px;top:136px;font-size:18px;color:#333}
.who p.body{position:absolute;left:110px;top:192px;width:460px;font-size:13.5px;line-height:24px;color:#555}
.who-photo{position:absolute;left:694px;top:63px;width:394px;height:315px;background:linear-gradient(135deg,#e9ecef,#b9c7d6 55%,#8aa0b8)}

/* services */
.services{top:1135px;height:766px;background:var(--grey-bg)}
.card{position:absolute;background:var(--white);border-radius:4px;box-shadow:0 2px 8px rgba(0,0,0,.08);overflow:hidden}
.card-img{height:175px}
.service-card{width:310px;height:371px;top:249px;text-align:center}
.service-card h3{margin-top:26px;font-weight:500;font-size:14px;color:#222;letter-spacing:.5px}
.service-card p{margin:14px auto 0;width:260px;font-size:12.5px;line-height:21px;color:var(--muted)}
.service-card .btn{left:87px;top:316px;width:137px;height:34px;font-size:11px}
.dots{position:absolute;left:0;width:1200px;display:flex;justify-content:center;gap:8px}
.dots span{width:9px;height:9px;border-radius:50%;border:1.5px solid #333}
.dots span.on{background:var(--red);border-color:var(--red)}
.skyline{position:absolute;left:0;top:670px;width:1200px;height:96px;background:linear-gradient(180deg,rgba(200,200,200,0),#d6d6d6)}

/* testimonials */
.testimonials{top:1901px;height:674px}
.t-card{position:absolute;left:198px;top:284px;width:804px;height:299px;border:1px solid var(--line);border-radius:8px;box-shadow:0 3px 10px rgba(0,0,0,.07);background:var(--white)}
.avatar{position:absolute;left:548px;top:240px;width:104px;height:104px;border-radius:50%;background:linear-gradient(160deg,#cfe3e6,#8fb5bb);border:3px solid #fff;box-shadow:0 2px 6px rgba(0,0,0,.15)}
.quote-mark{position:absolute;left:285px;top:318px;font-family:Georgia,serif;font-size:140px;line-height:1;color:#cfcfcf;font-weight:700}
.stars{position:absolute;left:0;width:1200px;top:358px;display:flex;justify-content:center;gap:4px}
.t-name{position:absolute;left:0;width:1200px;top:388px;text-align:center;font-weight:600;font-size:16px;color:#222}
.t-role{position:absolute;left:0;width:1200px;top:420px;text-align:center;font-size:12px;font-style:italic;color:var(--muted)}
.t-text{position:absolute;left:262px;width:676px;top:456px;text-align:center;font-size:12.5px;line-height:22px;color:#777}
.arrow{position:absolute;top:374px}

/* blog */
.blog{top:2575px;height:712px;background:var(--grey-bg)}
.blog-card{width:310px;height:373px;top:209px}
.meta{display:flex;align-items:center;gap:6px;margin:18px 0 0 22px;font-size:11px;color:#444;white-space:nowrap}
.meta svg{flex:none}
.meta .gap{width:14px}
.blog-card h3{margin:14px 0 0 22px;font-weight:500;font-size:14px;color:#222}
.blog-card p{margin:8px 0 0 22px;width:270px;font-size:12.5px;line-height:21px;color:var(--muted)}
.blog-card .more{display:block;margin:10px 0 0 22px;font-size:11px;color:#222;font-weight:500}

/* contact */
.contact{top:3287px;height:778px}
.contact-left h3{position:absolute;left:110px;top:228px;font-family:'Lato',sans-serif;font-weight:700;font-size:38px;line-height:50px;color:#222;white-space:nowrap}
.contact-left p{position:absolute;left:112px;top:345px;width:440px;font-family:'Lato',sans-serif;font-size:20px;line-height:33px;color:#444}
.contact-left a{color:var(--red);text-decoration:underline;font-weight:700;white-space:nowrap}
.field{position:absolute;height:52px;border:1.5px solid #bdbdbd;display:flex;align-items:center;padding-left:24px;font-size:15px;color:#666;background:#fff}
.form-note{position:absolute;left:590px;top:503px;width:445px;font-size:13px;line-height:23px;color:#888}
.contact .btn{left:590px;top:643px;width:218px;height:47px;font-size:15px}

/* footer */
.footer{top:4065px;height:450px;background:var(--footer);color:#ccc}
.f-logo{position:absolute;left:110px;top:92px;display:flex;align-items:center;gap:10px}
.f-logo .logo-name{color:#fff;font-size:28px}
.f-about{position:absolute;left:110px;top:200px;width:270px;font-size:12.5px;line-height:20px;color:#ccc}
.f-hours{position:absolute;left:113px;top:290px;font-size:12.5px;color:#ccc}
.f-col{position:absolute;top:88px;font-size:12.5px;color:#ddd;white-space:nowrap}
.f-col h4{color:var(--red);font-size:15px;font-weight:600;margin-bottom:30px;letter-spacing:.3px}
.f-col li{list-style:none;line-height:26px}
.social{display:flex;gap:10px;margin-top:14px}
.social span{width:16px;height:16px;border-radius:50%;border:2px solid var(--red)}
.c-row{display:flex;gap:20px;margin-bottom:12px;line-height:21px}
.c-row svg{flex:none;margin-top:3px}
.copyright{position:absolute;left:0;width:1200px;top:392px;text-align:center;font-size:11.5px;color:#bbb}
</style>
</head>
<body>

<header class="hero">
  <div class="hero-photo" role="img" aria-label="Bright home interior with a hand tapping a smart home control tablet"></div>
  <div class="logo"><span class="logo-dot"></span><span class="logo-name">BRIGHTGATE</span></div>
  <nav class="nav">
    <a class="active" style="left:0">Home</a>
    <a style="left:82px">About</a>
    <a style="left:163px">Packages</a>
    <a style="left:268px">Services &amp; Solutions</a>
    <a style="left:443px">ProductsWhy</a>
    <a style="left:573px">Resources</a>
  </nav>
  <span class="nav-divider"></span>
  <svg class="search" width="20" height="20" viewBox="0 0 20 20"><circle cx="8" cy="8" r="6" fill="none" stroke="#d3202a" stroke-width="2"/><line x1="12.5" y1="12.5" x2="18" y2="18" stroke="#d3202a" stroke-width="2"/></svg>
  <h1 class="hero-title">A GREAT PLACE FOR<br>YOUR <span class="red">SECURITY NEEDS</span></h1>
  <p class="hero-text">We offer alarm monitoring,security cameras, access control, gate openers, home theater systems, covert camera installations, Fire alarm installation and monitoring</p>
  <a class="btn" style="left:110px;top:433px;width:186px;height:44px;font-size:14px">Get Started</a>
</header>

<section class="who">
  <h2>WHO WE <span class="red">ARE</span></h2>
  <div class="lead">Over 25 Years Experience</div>
  <p class="body">Sed ut perspiciatis unde omnis iste natus error sit voluptatem accusantium doloremque laudantium, totam rem aperiam, eaque ipsa quae ab illo inventore veritatis et quasi architecto beatae vitae dicta sunt explicabo. Nemo enim ipsam voluptatem quia voluptas sit aspernatur aut odit aut fugit, sed quia consequuntur magni dolores eos qui ratione.</p>
  <a class="btn" style="left:110px;top:357px;width:186px;height:46px;font-size:14px">Read More</a>
  <div class="who-photo" role="img" aria-label="Technician smiling beside a wall-mounted security control panel"></div>
</section>

<section class="services">
  <h2 class="section-title" style="top:72px">OUR <span class="red">SERVICES</span></h2>
  <p class="section-sub" style="top:136px">Eoluptatem accusantium doloremque laudantium totam rem aperiam eaque ipsa quae ab illo inventore</p>

  <article class="card service-card" style="left:110px">
    <div class="card-img" role="img" aria-label="Resident using an access control keypad at the door" style="background:linear-gradient(135deg,#eceae6,#c9c3ba)"></div>
    <h3>ACCESS CONTROL</h3>
    <p>Rotam rem aperiam, eaque ipsa quae ab illo inventore veritatis et quasi architecto beatae vitae dicta sunt explicabo.</p>
    <a class="btn">Read More</a>
  </article>
  <article class="card service-card" style="left:445px">
    <div class="card-img" role="img" aria-label="Technicians installing an alarm monitoring panel" style="background:linear-gradient(135deg,#8a8e95,#3f5d8e)"></div>
    <h3>ALARM MONITORING</h3>
    <p>Rotam rem aperiam, eaque ipsa quae ab illo inventore veritatis et quasi architecto beatae vitae dicta sunt explicabo.</p>
    <a class="btn">Read More</a>
  </article>
  <article class="card service-card" style="left:780px">
    <div class="card-img" role="img" aria-label="Installer mounting a ceiling security camera" style="background:linear-gradient(135deg,#c9a27f,#7b5b45 60%,#2f4a7a)"></div>
    <h3>COVERT CAMERA INSTALLATIONS</h3>
    <p>Rotam rem aperiam, eaque ipsa quae ab illo inventore veritatis et quasi architecto beatae vitae dicta sunt explicabo.</p>
    <a class="btn">Read More</a>
  </article>

  <div class="dots" style="top:661px"><span class="on"></span><span></span><span></span></div>
  <div class="skyline" role="img" aria-label="Line drawing of a neighbourhood skyline"></div>
</section>

<section class="testimonials">
  <h2 class="section-title" style="top:84px">TESTIMONIALS</h2>
  <p class="section-sub" style="top:148px">Eeatae vitae dicta sunt explicaboemo enim ipsam voluptatem quia voluptas sit aspernatur aut odit aut fugit.</p>
  <div class="t-card"></div>
  <div class="avatar" role="img" aria-label="Portrait of the customer"></div>
  <div class="quote-mark">&ldquo;</div>
  <div class="stars">
    <svg width="14" height="14" viewBox="0 0 24 24"><path d="M12 2l3 7 7 .6-5.4 4.7 1.7 7.2L12 17.8 5.7 21.5l1.7-7.2L2 9.6 9 9z" fill="#f2b705"/></svg>
    <svg width="14" height="14" viewBox="0 0 24 24"><path d="M12 2l3 7 7 .6-5.4 4.7 1.7 7.2L12 17.8 5.7 21.5l1.7-7.2L2 9.6 9 9z" fill="#f2b705"/></svg>
    <svg width="14" height="14" viewBox="0 0 24 24"><path d="M12 2l3 7 7 .6-5.4 4.7 1.7 7.2L12 17.8 5.7 21.5l1.7-7.2L2 9.6 9 9z" fill="#f2b705"/></svg>
    <svg width="14" height="14" viewBox="0 0 24 24"><path d="M12 2l3 7 7 .6-5.4 4.7 1.7 7.2L12 17.8 5.7 21.5l1.7-7.2L2 9.6 9 9z" fill="#f2b705"/></svg>
    <svg width="14" height="14" viewBox="0 0 24 24"><path d="M12 2l3 7 7 .6-5.4 4.7 1.7 7.2L12 17.8 5.7 21.5l1.7-7.2L2 9.6 9 9z" fill="#f2b705"/></svg>
  </div>
  <div class="t-name">MARISOL T KEANE</div>
  <div class="t-role">Coluptate, CEO</div>
  <p class="t-text">"Sed ut perspiciatis unde omnis iste natus error sit voluptatem accusantium doloremque laudantium, totam rem aperiam, eaque ipsa quae ab illo inventore veritatis et quasi architecto beatae vitae dicta sunt explicabo. Nemo enim ipsam voluptatem quia voluptas sit aspernatur aut odit aut fugit, sed quia consequuntur magni dolores eos qui ratione voluptatem sequi nesciunt."</p>
  <svg class="arrow" style="left:52px" width="16" height="34" viewBox="0 0 16 34"><polyline points="14,2 2,17 14,32" fill="none" stroke="#333" stroke-width="2"/></svg>
  <svg class="arrow" style="left:1132px" width="16" height="34" viewBox="0 0 16 34"><polyline points="2,2 14,17 2,32" fill="none" stroke="#333" stroke-width="2"/></svg>
</section>

<section class="blog">
  <h2 class="section-title" style="top:72px">OUR <span class="red">BLOG</span></h2>
  <p class="section-sub" style="top:138px;left:200px;width:800px">Eoluptatem Rccusantium ToloremqueEaudantium Yotamrem Aperiam</p>

  <article class="card blog-card" style="left:110px">
    <div class="card-img" role="img" aria-label="Hands holding a tablet with a security app" style="background:linear-gradient(135deg,#e3dccf,#9f8f78)"></div>
    <div class="meta">
      <svg width="12" height="12" viewBox="0 0 12 12"><circle cx="6" cy="3.5" r="3" fill="#d3202a"/><path d="M0 12c0-3.5 2.7-5 6-5s6 1.5 6 5z" fill="#d3202a"/></svg>Dorian Velk<span class="gap"></span>
      <svg width="13" height="12" viewBox="0 0 13 12"><rect x=".5" y="1.5" width="12" height="10" fill="none" stroke="#d3202a"/><line x1=".5" y1="4.5" x2="12.5" y2="4.5" stroke="#d3202a"/></svg>Mar, 2020
    </div>
    <h3>VOLUPTATEM ACCUSANT</h3>
    <p>Rotam rem aperiam, eaque ipsa quae ab illo inventore veritatis et quasi architecto beatae vitae dicta sunt explicabo.</p>
    <a class="more">READ MORE</a>
  </article>
  <article class="card blog-card" style="left:445px">
    <div class="card-img" role="img" aria-label="Woman using a wall-mounted home control panel" style="background:linear-gradient(135deg,#e6e8ea,#a9b3bd)"></div>
    <div class="meta">
      <svg width="12" height="12" viewBox="0 0 12 12"><circle cx="6" cy="3.5" r="3" fill="#d3202a"/><path d="M0 12c0-3.5 2.7-5 6-5s6 1.5 6 5z" fill="#d3202a"/></svg>Elna Strober<span class="gap"></span>
      <svg width="13" height="12" viewBox="0 0 13 12"><rect x=".5" y="1.5" width="12" height="10" fill="none" stroke="#d3202a"/><line x1=".5" y1="4.5" x2="12.5" y2="4.5" stroke="#d3202a"/></svg>Mar, 2020
    </div>
    <h3>UPTATEM QUIA VOLUPTAS</h3>
    <p>Rotam rem aperiam, eaque ipsa quae ab illo inventore veritatis et quasi architecto beatae vitae dicta sunt explicabo.</p>
    <a class="more">READ MORE</a>
  </article>
  <article class="card blog-card" style="left:780px">
    <div class="card-img" role="img" aria-label="Phone showing a camera app beside a wall camera" style="background:linear-gradient(135deg,#f2f2f2,#c4c4c4)"></div>
    <div class="meta">
      <svg width="12" height="12" viewBox="0 0 12 12"><circle cx="6" cy="3.5" r="3" fill="#d3202a"/><path d="M0 12c0-3.5 2.7-5 6-5s6 1.5 6 5z" fill="#d3202a"/></svg>Tobias Renfro<span class="gap"></span>
      <svg width="13" height="12" viewBox="0 0 13 12"><rect x=".5" y="1.5" width="12" height="10" fill="none" stroke="#d3202a"/><line x1=".5" y1="4.5" x2="12.5" y2="4.5" stroke="#d3202a"/></svg>Mar, 2020
    </div>
    <h3>QUIANON NUMQUAM</h3>
    <p>Rotam rem aperiam, eaque ipsa quae ab illo inventore veritatis et quasi architecto beatae vitae dicta sunt explicabo.</p>
    <a class="more">READ MORE</a>
  </article>

  <div class="dots" style="top:617px"><span class="on"></span><span></span><span></span></div>
</section>

<section class="contact">
  <h2 class="section-title" style="top:72px">CONTACT <span class="red">US</span></h2>
  <p class="section-sub" style="top:138px">Eagni dolores eosqui ratione voluptatem sequi nesciunt</p>
  <div class="contact-left">
    <h3>Get a free quote and<br><span class="red">Brightgate</span> offers.</h3>
    <p>Orte natus error sit voluptatem accusantium doloremque laudantium, totam rem <a>832-555-0147</a> ipsa quae ab illo inventore veritatis et quasi architecto beatae vitae dicta sunt explicabomo enim ipsam</p>
  </div>
  <div class="field" style="left:587px;top:226px;width:447px">Name</div>
  <div class="field" style="left:587px;top:310px;width:447px">Email</div>
  <div class="field" style="left:587px;top:392px;width:200px">Phone</div>
  <div class="field" style="left:832px;top:392px;width:200px">Zip</div>
  <p class="form-note">Eaed quia consequuntur magni dolores eos qui ratione voluptatem sequi nesciunt. Neque porro quisquam est, qui dolorem ipsum quia dolor sit amet, consectetur, adipisci velit, sed quia non numquam eius modi tempora incidunt ut labore et dolore magnam aliquam quaerat voluptatem. Ut enim ad minima veniam</p>
  <a class="btn">Get a Free Quote</a>
</section>

<footer class="footer">
  <div class="f-logo"><span class="logo-dot"></span><span class="logo-name">BRIGHTGATE</span></div>
  <p class="f-about">Rotam rem aperiam, eaque ipsa quae ab illo inventore veritatis et quasi architecto beatae vitae dicta sunt explicabo.</p>
  <div class="f-hours">Monday-Friday 8am-5pm</div>

  <div class="f-col" style="left:405px">
    <h4>QUICK LINKS</h4>
    <ul><li>Home</li><li>About</li><li>Packages</li><li>Services &amp; Solutions</li><li>ProductsWhy QMR</li><li>Resources</li></ul>
  </div>
  <div class="f-col" style="left:573px">
    <h4>LINKS</h4>
    <ul><li>Privacy policy</li><li>Terms and Conditions</li><li>Contact Us</li></ul>
  </div>
  <div class="f-col" style="left:734px">
    <h4>LICENSE</h4>
    <ul><li>license #K41862509</li><li>Fire license# MTQ-6071852</li><li>LUV-8146027</li></ul>
    <div class="social"><span></span><span></span><span></span></div>
  </div>
  <div class="f-col" style="left:915px;width:240px">
    <h4>CONTACT US</h4>
    <div class="c-row">
      <svg width="12" height="16" viewBox="0 0 12 16"><path d="M6 0a6 6 0 0 1 6 6c0 4-6 10-6 10S0 10 0 6a6 6 0 0 1 6-6z" fill="#d3202a"/><circle cx="6" cy="6" r="2.2" fill="#121212"/></svg>
      <span>P.O. Box 419 Marren Falls,<br>NV 77519,<br>USA</span>
    </div>
    <div class="c-row">
      <svg width="13" height="13" viewBox="0 0 24 24"><path d="M6.6 10.8a15 15 0 0 0 6.6 6.6l2.2-2.2a1 1 0 0 1 1-.25 11.4 11.4 0 0 0 3.6.6 1 1 0 0 1 1 1V20a1 1 0 0 1-1 1A17 17 0 0 1 3 4a1 1 0 0 1 1-1h3.5a1 1 0 0 1 1 1c0 1.25.2 2.45.6 3.6a1 1 0 0 1-.25 1z" fill="#d3202a"/></svg>
      <span>832-555-0147</span>
    </div>
    <div class="c-row">
      <svg width="14" height="11" viewBox="0 0 14 11"><rect x=".5" y=".5" width="13" height="10" fill="none" stroke="#d3202a"/><polyline points=".5,.5 7,6 13.5,.5" fill="none" stroke="#d3202a"/></svg>
      <span>Brightgatesys@kelvamail.com</span>
    </div>
  </div>

  <div class="copyright">Copyright &copy; 2020. All rights reserved.</div>
</footer>

</body>
</html>
```